Veltrane Group Business Card Design

The CEO is looking for a new trendy look for his business card.
You can stay with current branding or come up with something new/creative. It can be 3D, including Medical Office buildings. You can use our logo in a variety of colors. Please include name, title, company name, company website, email address, cell number

Target Market(s)

Real Estate Development and Construction

Industry/Entity Type

Health care real estate

Contact Information for Business Card

Rohesh Kamdar, CEO M-604.781.2249 E-roheshkamdar@veltrane.com Address:4180 Lindqvist Ave, Tampa, FL 33482 www.veltrane.com

Font styles to use
Other font styles liked:
• Be creative

Requirements
Must have
• Creative, trendy look
Nice to have
• Please go to our website to get a feel- www. veltrane.com
Should not have
• small fonts

```html
<!DOCTYPE html>
<html lang="en">
<head>
<meta charset="utf-8">
<title>Veltrane Group Business Card</title>
<link rel="stylesheet" href="https://fonts.googleapis.com/css2?family=Montserrat:wght@400;700;900&display=swap">
<style>
  :root {
    --stage: #3a3a3a;
    --card-dark: #141414;
    --card-light: #ffffff;
    --ink: #111111;
    --ink-soft: #333333;
    --paper-text: #ffffff;
  }
  * { margin: 0; padding: 0; box-sizing: border-box; }
  html, body {
    width: 1200px; height: 875px; overflow: hidden;
    background: var(--stage);
    font-family: "Montserrat", sans-serif;
  }
  .sheet {
    position: relative; width: 1200px; height: 875px;
  }
  .card {
    position: absolute; width: 620px; height: 354px;
    border-radius: 26px;
    left: 290px;
  }
  .card--front { top: 64px; background: var(--card-dark); }
  .card--back { top: 458px; background: var(--card-light); }

  .wordmark {
    position: absolute; font-weight: 900; line-height: 1;
    display: flex; flex-direction: column; align-items: flex-end;
  }
  .wordmark__name { letter-spacing: -2px; }
  .card--front .wordmark {
    color: var(--paper-text);
    left: 50%; top: 50%; transform: translate(-50%, -50%);
  }
  .card--front .wordmark__name { font-size: 96px; }
  .card--front .wordmark__sub { font-size: 46px; margin-top: 2px; }

  .card--back .wordmark {
    color: var(--ink);
    left: 48px; top: 148px;
  }
  .card--back .wordmark__name { font-size: 52px; letter-spacing: -1px; }
  .card--back .wordmark__sub { font-size: 26px; margin-top: 2px; }

  .divider {
    position: absolute; left: 322px; top: 96px;
    width: 2px; height: 170px; background: var(--ink);
  }
  .contact {
    position: absolute; left: 342px; top: 92px;
    color: var(--ink-soft);
  }
  .contact__name { font-size: 22px; font-weight: 700; color: var(--ink); }
  .contact__title { font-size: 13px; margin-top: 2px; }
  .contact__address { font-size: 13px; line-height: 1.35; margin-top: 12px; }
  .contact__list { list-style: none; margin-top: 12px; }
  .contact__item {
    display: flex; align-items: center; gap: 8px;
    font-size: 13px; line-height: 1; margin-bottom: 9px;
  }
  .contact__icon { width: 12px; height: 12px; flex: none; }
</style>
</head>
<body>
<main class="sheet">
  <section class="card card--front">
    <div class="wordmark">
      <span class="wordmark__name">Veltrane</span>
      <span class="wordmark__sub">group</span>
    </div>
  </section>

  <section class="card card--back">
    <div class="wordmark">
      <span class="wordmark__name">Veltrane</span>
      <span class="wordmark__sub">group</span>
    </div>
    <div class="divider"></div>
    <div class="contact">
      <p class="contact__name">Rohesh Kamdar</p>
      <p class="contact__title">CEO</p>
      <p class="contact__address">4180 Lindqvist Ave,<br>Tampa, FL 33482</p>
      <ul class="contact__list">
        <li class="contact__item">
          <svg class="contact__icon" viewBox="0 0 24 24" aria-hidden="true"><path fill="#111" d="M6.6 10.8a15.1 15.1 0 0 0 6.6 6.6l2.2-2.2a1 1 0 0 1 1-.25 11.4 11.4 0 0 0 3.6.57 1 1 0 0 1 1 1V20a1 1 0 0 1-1 1A17 17 0 0 1 3 4a1 1 0 0 1 1-1h3.5a1 1 0 0 1 1 1c0 1.25.2 2.45.57 3.57a1 1 0 0 1-.25 1z"/></svg>
          604.781.2249
        </li>
        <li class="contact__item">
          <svg class="contact__icon" viewBox="0 0 24 24" aria-hidden="true"><path fill="#111" d="M2 5h20v14H2z"/><path fill="none" stroke="#fff" stroke-width="2" d="M3 6l9 7 9-7"/></svg>
          roheshkamdar@veltrane.com
        </li>
        <li class="contact__item">
          <svg class="contact__icon" viewBox="0 0 24 24" aria-hidden="true"><circle cx="12" cy="12" r="10" fill="#111"/><path fill="none" stroke="#fff" stroke-width="1.5" d="M2 12h20M12 2c3 3 3 17 0 20M12 2c-3 3-3 17 0 20"/></svg>
          www.veltrane.com
        </li>
      </ul>
    </div>
  </section>
</main>
</body>
</html>
```